Plotvista Caribbean

We need a vibrant, user friendly and exciting website for our land search company called "plotVista" This application will help individuals locate and or list lots for sale within the Caribbean. We will offer a small cash back incentive to buyers that purchase land from our site, and we will charge a 1%-2% success fee to our sellers once a successful transaction is made. We would like to become a match making site, matching buyers and sellers on our platform. We will also include a service directory and marketing advertisement spot for other service providers for a fee. We would like to see a webdesign incorporating Caribbean colors (blue, green and yellow) with very modern clean lines, very picturesque and easy to use.

Industry/Entity Type

Real Estate

Coding

Coded - Design and coding required

Number of Pages Required

5+ page

Font styles to use
Sans Serif

Colors
ffffff
85acd3
b768aa
dbdbdb

Requirements
Nice to have
• Scenic photos of the ocean and beautiful landscape

```html
<!DOCTYPE html>
<html lang="en">
<head>
<meta charset="utf-8">
<title>plotVista – Land Search</title>
<link href="https://fonts.googleapis.com/css2?family=Nunito:wght@300;400;600&family=Open+Sans:wght@400;600&display=swap" rel="stylesheet">
<style>
:root{
  --white:#ffffff;
  --sky:#85acd3;
  --plum:#b768aa;
  --mist:#dbdbdb;
  --band:#efefef;
  --ink:#2b2b2b;
  --text:#666666;
  --dark:#1c1c1c;
  --darker:#111111;
  --panel:rgba(20,22,24,.82);
}
*{box-sizing:border-box;margin:0;padding:0}
html,body{width:1200px;height:2659px;overflow:hidden;background:var(--white)}
body{position:relative;font-family:"Open Sans",Arial,sans-serif;color:var(--ink)}
.abs{position:absolute}
.heading{font-family:"Nunito",Arial,sans-serif;font-weight:400;color:#333;letter-spacing:.5px}
/* hero */
.hero{left:0;top:0;width:1200px;height:583px;
  background:linear-gradient(180deg,#8fa3b0 0%,#a9b8b3 14%,#7f9a6a 26%,#5f8a3e 45%,#4f7f33 70%,#3e6d2a 100%)}
.logo{left:89px;top:34px;font-family:"Nunito",sans-serif;font-weight:600;font-size:37px;color:var(--white)}
.nav a{position:absolute;top:48px;font-size:16px;color:var(--white);text-decoration:none;letter-spacing:.3px}
.nav a.active{border-bottom:1px solid var(--white);padding-bottom:4px}
.login{left:1016px;top:43px;width:95px;height:31px;border-radius:16px;background:var(--plum);color:var(--white);font-size:16px;text-align:center;line-height:31px}
.search-panel{left:269px;top:245px;width:662px;height:214px;background:var(--panel)}
.tab{position:absolute;top:0;height:53px;line-height:53px;text-align:center;color:var(--white);font-size:17px}
.tab-buy{left:0;width:326px;background:#1e2124}
.tab-sell{left:334px;width:328px;background:var(--sky)}
.search-title{position:absolute;top:71px;width:100%;text-align:center;font-family:"Nunito",sans-serif;font-size:38px;color:var(--white)}
.search-field{position:absolute;left:39px;top:131px;width:532px;height:53px;background:var(--white);font-size:12px;color:#555;line-height:53px;padding-left:20px}
.search-btn{position:absolute;left:571px;top:131px;width:55px;height:53px;background:var(--sky)}
.hero-dot{width:26px;height:26px;border-radius:50%;background:rgba(30,30,30,.55);top:326px}
/* listings */
.section-title{width:1200px;text-align:center;font-size:32px}
.card{background:var(--white);box-shadow:0 1px 4px rgba(0,0,0,.25);text-align:center}
.card-photo{display:block;width:100%}
.price{font-size:19px;color:#333;margin-top:14px}
.meta{font-size:12px;color:#555;line-height:20px}
.chev{width:22px;height:40px}
/* what we do */
.band{left:0;width:1200px;background:var(--band)}
.body-copy{font-size:13px;line-height:23px;color:var(--text)}
.pill{background:var(--plum);color:var(--white);font-size:13px;border-radius:17px;text-align:center;box-shadow:0 2px 3px rgba(0,0,0,.2)}
.video{left:642px;top:1122px;width:469px;height:280px;background:#111}
/* contact */
.field{position:absolute;background:var(--white);border:1px solid #cfcfcf;box-shadow:inset 0 1px 2px rgba(0,0,0,.08);font-size:12px;color:#444;padding-left:14px;line-height:48px}
/* footer */
.footer{left:0;top:2347px;width:1200px;height:250px;background:var(--dark);color:var(--white)}
.foot-title{position:absolute;top:62px;font-family:"Nunito",sans-serif;font-size:17px;letter-spacing:.3px}
.foot-text{position:absolute;font-size:13px;line-height:26px}
.copyright{left:0;top:2597px;width:1200px;height:62px;background:var(--darker);color:var(--white);font-size:12px;text-align:center;line-height:62px}
.social{position:absolute;left:0;display:flex;align-items:center;gap:16px;font-size:13px}
.social i{display:block;width:34px;height:34px;border:1px solid #888;border-radius:50%}
</style>
</head>
<body>

<!-- hero -->
<header class="abs hero" role="img" aria-label="Aerial photo of green farmland fields under a hazy sky"></header>
<div class="abs logo">plotVista</div>
<nav class="nav">
  <a class="active" style="left:472px">HOME</a>
  <a style="left:556px">ABOUT</a>
  <a style="left:644px">BUY</a>
  <a style="left:712px">SELL</a>
  <a style="left:783px">BROKERS</a>
  <a style="left:888px">CONTACT US</a>
</nav>
<div class="abs login">LOGIN</div>

<div class="abs hero-dot" style="left:70px"><svg width="26" height="26"><path d="M15 8l-5 5 5 5" fill="none" stroke="#fff" stroke-width="2"/></svg></div>
<div class="abs hero-dot" style="left:1102px"><svg width="26" height="26"><path d="M11 8l5 5-5 5" fill="none" stroke="#fff" stroke-width="2"/></svg></div>

<section class="abs search-panel">
  <div class="tab tab-buy">BUY</div>
  <div class="tab tab-sell">SELL</div>
  <h1 class="search-title">LAND SEARCH</h1>
  <div class="search-field">SEARCH</div>
  <div class="search-btn"><svg width="55" height="53"><circle cx="26" cy="25" r="7" fill="none" stroke="#fff" stroke-width="3"/><path d="M31 30l6 6" stroke="#fff" stroke-width="3" stroke-linecap="round"/></svg></div>
</section>

<!-- new listings -->
<h2 class="abs heading section-title" style="top:652px">NEW LISTINGS</h2>
<svg class="abs chev" style="left:53px;top:841px"><path d="M20 2L3 20l17 18" fill="none" stroke="#888" stroke-width="1.5"/></svg>
<svg class="abs chev" style="left:1130px;top:841px"><path d="M2 2l17 18L2 38" fill="none" stroke="#888" stroke-width="1.5"/></svg>

<article class="abs card" style="left:90px;top:727px;width:241px;height:255px">
  <div class="card-photo" style="height:147px;background:linear-gradient(180deg,#c8d6e2 0%,#b7c6b3 30%,#8a7a55 55%,#6f6a3e 100%)" role="img" aria-label="Ploughed field with a lone tree and mountains"></div>
  <div class="price">$2,600,000</div>
  <div class="meta">218 Coral Bay Rd, Montego<br>4 bd3 ba2,423 sq ft</div>
</article>
<article class="abs card" style="left:349px;top:727px;width:241px;height:255px">
  <div class="card-photo" style="height:147px;background:linear-gradient(180deg,#6aa33a,#4f8f2a)" role="img" aria-label="Green lawn with a land for sale sign"></div>
  <div class="price">$1,300,000</div>
  <div class="meta">218 Coral Bay Rd, Montego<br>4 bd3 ba2,423 sq ft</div>
</article>
<article class="abs card" style="left:608px;top:727px;width:241px;height:255px">
  <div class="card-photo" style="height:147px;background:linear-gradient(180deg,#e7d7b4 0%,#b59a6c 40%,#8b6a44 100%)" role="img" aria-label="Dry empty lot at sunset"></div>
  <div class="price">$3,200,000</div>
  <div class="meta">218 Coral Bay Rd, Montego<br>4 bd3 ba2,423 sq ft</div>
</article>
<article class="abs card" style="left:867px;top:727px;width:241px;height:255px">
  <div class="card-photo" style="height:147px;background:linear-gradient(180deg,#8fb7e0 0%,#c9dcef 35%,#7aa348 60%,#5f8d30 100%)" role="img" aria-label="Rolling green hills under blue sky"></div>
  <div class="price">$1,600,000</div>
  <div class="meta">218 Coral Bay Rd, Montego<br>4 bd3 ba2,423 sq ft</div>
</article>

<!-- what we do -->
<section class="abs band" style="top:1056px;height:430px"></section>
<h2 class="abs heading" style="left:92px;top:1138px;font-size:26px">WHAT WE DO</h2>
<div class="abs body-copy" style="left:92px;top:1182px;width:502px">
  <p>We will offer a small cash back incentive to buyers that purchase land from our site, and we will charge a 1%-2% success fee to our sellers once a successful transaction is made.</p>
  <p style="margin-top:4px">It has survived not only five centuries, but also the leap into electronic typesetting, remaining essentially unchanged. It was popularised in the 1960s with the release of Typeset Co sheets containing Lorem Ipsum passages, and more recently. with desktop publishing software like PageForge Pro including versions</p>
</div>
<div class="abs pill" style="left:92px;top:1354px;width:112px;height:32px;line-height:32px">READ MORE</div>

<div class="abs video">
  <div class="abs" style="left:0;top:26px;width:469px;height:228px;background:linear-gradient(180deg,#7fb1e6 0%,#b9d6ef 25%,#5f8f3a 40%,#9a7550 55%,#8a6440 100%)" role="img" aria-label="Video still of a bare field with green trees behind"></div>
  <svg class="abs" style="left:198px;top:114px" width="74" height="52"><rect width="74" height="52" rx="12" fill="#1a1a1a" opacity=".9"/><path d="M29 15l20 11-20 11z" fill="#fff"/></svg>
  <svg class="abs" style="left:0;top:252px" width="469" height="28"><rect y="0" width="469" height="3" fill="#555"/><path d="M18 10v10l8-5z" fill="#ccc"/><path d="M50 12h4l4-3v12l-4-3h-4z" fill="#ccc"/><rect x="438" y="9" width="12" height="11" fill="none" stroke="#ccc" stroke-width="2"/></svg>
</div>

<!-- buyers and sellers -->
<h2 class="abs heading section-title" style="top:1567px">BUYERS AND SELLERS</h2>
<svg class="abs chev" style="left:69px;top:1768px"><path d="M20 2L3 20l17 18" fill="none" stroke="#888" stroke-width="1.5"/></svg>
<svg class="abs chev" style="left:1112px;top:1768px"><path d="M2 2l17 18L2 38" fill="none" stroke="#888" stroke-width="1.5"/></svg>

<article class="abs card" style="left:126px;top:1645px;width:291px;height:246px">
  <div class="card-photo" style="height:156px;background:linear-gradient(180deg,#c9d9e6 0%,#9eb27c 25%,#6aa23a 45%,#5a952c 100%)" role="img" aria-label="Green meadow with farmhouses in the distance"></div>
  <div class="price">$1,600,000</div>
  <div class="meta">218 Coral Bay Rd, Montego<br>4 bd3 ba2,423 sq ft</div>
</article>
<article class="abs card" style="left:443px;top:1645px;width:291px;height:246px">
  <div class="card-photo" style="height:156px;background:linear-gradient(180deg,#3f6b2a 0%,#8fb54a 45%,#c8d65e 65%,#7aa23a 100%)" role="img" aria-label="Sunlit grassy park lined with trees"></div>
  <div class="price">$3,200,000</div>
  <div class="meta">218 Coral Bay Rd, Montego<br>4 bd3 ba2,423 sq ft</div>
</article>
<article class="abs card" style="left:760px;top:1645px;width:291px;height:246px">
  <div class="card-photo" style="height:156px;background:linear-gradient(90deg,#4f8f34 0%,#5fa03c 60%,#3a3d42 100%)" role="img" aria-label="Handshake over green farmland"></div>
  <div class="price">$1,500,000</div>
  <div class="meta">218 Coral Bay Rd, Montego<br>4 bd3 ba2,423 sq ft</div>
</article>

<!-- about & contact -->
<section class="abs band" style="top:1969px;height:376px"></section>
<h2 class="abs heading" style="left:90px;top:2028px;font-size:26px">ABOUT US</h2>
<p class="abs body-copy" style="left:90px;top:2072px;width:467px;text-align:justify">Lorem Ipsum has been the industry's standard dummy text ever since the 1500s, when an unknown printer took a galley of type and scrambled it to make a type specimen book. It has survived not only five centuries, but also the leap into electronic typesetting, remaining essentially unchanged. It was popularised in the 1960s with the release of Typeset Co sheets containing Lorem Ipsum passages, and more recently with desktop publishing software like PageForge Pro including versions of Lorem Ipsum</p>

<h2 class="abs heading" style="left:636px;top:2027px;font-size:26px">CONTACT FORM</h2>
<form>
  <div class="field" style="left:640px;top:2081px;width:225px;height:50px">Name</div>
  <div class="field" style="left:881px;top:2081px;width:225px;height:50px">Email id</div>
  <div class="field" style="left:640px;top:2143px;width:225px;height:50px">Phone</div>
  <div class="field" style="left:881px;top:2143px;width:225px;height:50px">Subject</div>
  <div class="field" style="left:640px;top:2201px;width:466px;height:50px">Message</div>
</form>
<div class="abs pill" style="left:1008px;top:2265px;width:98px;height:34px;line-height:34px;font-size:15px">SUBMIT</div>

<!-- footer -->
<footer class="abs footer">
  <div class="foot-title" style="left:90px">NEWSLETTERS SIGN UP</div>
  <div class="foot-text" style="left:90px;top:94px;line-height:18px;width:250px">Sign up for our daily email by entering your information below</div>
  <div class="abs" style="left:90px;top:143px;width:214px;height:29px;background:#ececec;color:#666;font-size:12px;line-height:29px;padding-left:10px">Email address</div>
  <div class="abs" style="left:90px;top:188px;width:95px;height:29px;background:var(--plum);font-size:12px;line-height:29px;text-align:center">SUBSCRIBE</div>

  <div class="foot-title" style="left:386px">LATEST TWEET</div>
  <div class="foot-text" style="left:386px;top:98px;line-height:20px">
    <span style="display:inline-block;width:13px;height:13px;border-radius:50%;background:#fff;margin-right:10px"></span>Featured Workspace : Bluecrest Studio<br>
    <span style="padding-left:23px">plv.to/8KdrT2 <i>10 hours ago</i></span>
  </div>
  <div class="foot-text" style="left:386px;top:156px;line-height:20px">
    <span style="display:inline-block;width:13px;height:13px;border-radius:50%;background:#fff;margin-right:10px"></span>Featured Workspace : Bluecrest Studio<br>
    <span style="padding-left:23px">plv.to/8KdrT2 <i>10 hours ago</i></span>
  </div>

  <div class="foot-title" style="left:705px">GET IN TOUCH</div>
  <div class="foot-text" style="left:710px;top:96px">Address : 46 Harbour View Ln<br>Kingston, JM 10025<br>Phone : 876-555-0148<br>Email : hello@plotvista.example</div>

  <div class="foot-title" style="left:962px">FOLLOW US ON</div>
  <div class="abs" style="left:962px;top:0">
    <div class="social" style="top:111px"><i></i>Friendnet</div>
    <div class="social" style="top:155px"><i></i>Chirpline</div>
    <div class="social" style="top:198px"><i></i>Picstream</div>
  </div>
</footer>
<div class="abs copyright">Copyright © 2017. All Rights Reserved</div>

</body>
</html>
```